Business card update

Opening a subsidiary of my company in the USA and need to update my logo.
Updates

Reason: Give more time to a good design.

I made a mistake on my briefing. It's only the business card. Thanks for alerting me on the mistake.

All the best

Teodoro

Target Market(s)

We are an Executive Search company and our target audience are executives in large corporations.

Industry/Entity Type

Business

Requirements
Must have
• Keep the logo. In the US the company is called Delia Brunet Executive Search.

```html
<!DOCTYPE html>
<html lang="en">
<head>
<meta charset="utf-8">
<title>Delia Brunet Executive Search – Business Card</title>
<link rel="stylesheet" href="https://fonts.googleapis.com/css2?family=Questrial&display=swap">
<style>
  :root {
    --backdrop: #4d5a5c;
    --card-white: #ffffff;
    --card-teal: #46d9b7;
    --teal-deep: #2fb596;
    --navy: #1f2f5c;
    --ink: #1d3a40;
    --name-white: #ffffff;
    --phone-red: #d62a2a;
  }
  * { box-sizing: border-box; margin: 0; padding: 0; }
  html, body {
    width: 1200px;
    height: 741px;
    overflow: hidden;
    background: var(--backdrop);
    font-family: "Questrial", sans-serif;
  }
  .canvas {
    position: relative;
    width: 1200px;
    height: 741px;
  }
  .business-card {
    position: absolute;
    left: 485px;
    top: 158px;
    width: 238px;
    height: 412px;
    background: var(--card-teal);
    box-shadow: 0 4px 10px rgba(0, 0, 0, 0.35);
    overflow: hidden;
  }
  .card-header {
    height: 80px;
    background: var(--card-white);
    display: flex;
    align-items: center;
    justify-content: center;
  }
  .brand-name {
    color: var(--navy);
    font-size: 15px;
    letter-spacing: 3px;
    white-space: nowrap;
  }
  .person-name {
    position: absolute;
    left: 10px;
    top: 101px;
    color: var(--name-white);
    font-size: 17px;
  }
  .phone {
    position: absolute;
    left: 10px;
    top: 138px;
    display: flex;
    align-items: center;
    gap: 5px;
    color: var(--ink);
    font-size: 13px;
  }
  .contact-list {
    position: absolute;
    left: 15px;
    top: 217px;
    list-style: none;
    color: var(--ink);
    font-size: 10.5px;
    line-height: 15px;
  }
  .contact-list li {
    display: flex;
    align-items: center;
    gap: 5px;
  }
  .company-name {
    position: absolute;
    left: 0;
    right: 0;
    top: 351px;
    text-align: center;
    color: var(--teal-deep);
    font-size: 15.5px;
    white-space: nowrap;
  }
  .address {
    position: absolute;
    left: 0;
    right: 0;
    top: 375px;
    text-align: center;
    color: var(--ink);
    font-size: 10.5px;
    line-height: 15px;
  }
  .address-line-rule {
    display: flex;
    align-items: center;
    gap: 6px;
  }
  .address-line-rule::before,
  .address-line-rule::after {
    content: "";
    flex: 1;
    height: 1px;
    background: var(--teal-deep);
  }
</style>
</head>
<body>
<main class="canvas">
  <article class="business-card">
    <header class="card-header">
      <span class="brand-name">DELIA BRUNET</span>
    </header>

    <h1 class="person-name">Teodoro S. Brunet</h1>

    <p class="phone">
      <svg width="10" height="12" viewBox="0 0 10 12" aria-hidden="true">
        <path d="M2 0.5 L4 3 L3 4.5 C3.5 6.5 4.8 8 6.3 8.8 L7.6 7.8 L9.6 10 L8 11.5 C4 11 1 7 0.5 2.2 Z" fill="var(--phone-red)"/>
      </svg>
      305 555-0147
    </p>

    <ul class="contact-list">
      <li>
        <svg width="11" height="8" viewBox="0 0 11 8" aria-hidden="true">
          <rect x="0.5" y="0.5" width="10" height="7" fill="#ffffff"/>
          <path d="M0.5 0.5 L5.5 4.5 L10.5 0.5" fill="none" stroke="var(--card-teal)" stroke-width="1"/>
        </svg>
        www.dbexecutivesearch.com
      </li>
      <li>
        <svg width="11" height="11" viewBox="0 0 11 11" aria-hidden="true">
          <circle cx="5.5" cy="5.5" r="5" fill="#ffffff"/>
          <path d="M3 2.5 C4.5 3 4 5 5.5 5.5 C6.5 6 6 8 7 9" fill="none" stroke="var(--card-teal)" stroke-width="1.2"/>
        </svg>
        tbrunet@dbexecutivesearch.com
      </li>
    </ul>

    <p class="company-name">Delia Brunet Executive Search</p>
    <address class="address">
      <span class="address-line-rule">4870 Harbor Crest Blvd Suite 200</span>
      <span>Coral Bay FL 33990</span>
    </address>
  </article>
</main>
</body>
</html>
```